Business Card Design Project

Business Card
We are rebranding with a new logo
Industry/Entity Type
Business
Contact Information for Business Card
Dennis Morvale +61 487215963 dennis@quorv.com.au P.O. Box 872 Fernlow QLD 4309
Requirements
Must have
- Logo

```html
<!DOCTYPE html>
<html lang="en">
<head>
<meta charset="utf-8">
<title>Quorv International – Business Card</title>
<link rel="stylesheet" href="https://fonts.googleapis.com/css2?family=Roboto:wght@400&family=Roboto+Condensed:wght@500;700&display=swap">
<style>
  :root {
    --backdrop: #1f1f1f;
    --card: #f2f2f2;
    --brand-blue: #1a9ad6;
    --band-blue: #1aa0dc;
    --band-blue-deep: #0f6f9e;
    --band-orange: #f0922a;
    --text-grey: #555555;
    --divider: #c9c9c9;
  }
  * { margin: 0; padding: 0; box-sizing: border-box; }
  html, body {
    width: 1200px; height: 960px; overflow: hidden;
    background: var(--backdrop);
  }
  .business-card {
    position: absolute; left: 314px; top: 294px;
    width: 600px; height: 342px;
    background: var(--card);
    border-radius: 18px;
    overflow: hidden;
  }
  .bottom-band {
    position: absolute; left: 0; right: 0; bottom: 0; height: 14px;
    background: linear-gradient(var(--band-blue), var(--band-blue-deep));
    border-top: 3px solid var(--band-orange);
  }
  .brand-name {
    position: absolute; left: 110px; top: 160px;
    width: 186px; text-align: center;
    font-family: "Roboto Condensed", sans-serif; font-weight: 700;
    font-size: 23px; letter-spacing: 0.5px; text-transform: uppercase;
    color: var(--brand-blue);
    transform: translateY(-50%);
  }
  .brand-dot {
    display: block; width: 14px; height: 14px; border-radius: 50%;
    background: var(--brand-blue); margin: 0 auto 8px;
  }
  .divider {
    position: absolute; left: 302px; top: 100px;
    width: 2px; height: 146px;
    background: linear-gradient(transparent, var(--divider) 20%, var(--divider) 80%, transparent);
  }
  .contact-block {
    position: absolute; left: 330px; top: 102px;
    font-family: "Roboto", sans-serif; font-size: 14.5px;
    color: var(--text-grey); line-height: 18.5px;
  }
  .person-name {
    font-family: "Roboto Condensed", sans-serif; font-weight: 700;
    font-size: 21px; color: var(--brand-blue); line-height: 26px;
    margin-bottom: 10px;
  }
  .postal-address { margin-bottom: 7px; }
  .contact-line { display: flex; align-items: center; gap: 8px; }
  .contact-line svg { width: 14px; height: 14px; fill: var(--brand-blue); flex: none; }
</style>
</head>
<body>
  <div class="business-card">
    <div class="brand-name"><span class="brand-dot"></span>Quorv International</div>
    <div class="divider"></div>
    <div class="contact-block">
      <div class="person-name">DENNIS MORVALE</div>
      <div class="postal-address">P.O. Box 872<br>Fernlow QLD 4309</div>
      <div class="contact-line">
        <svg viewBox="0 0 24 24"><path d="M6.6 10.8a15.1 15.1 0 0 0 6.6 6.6l2.2-2.2c.3-.3.7-.4 1-.2 1.1.4 2.3.6 3.6.6.6 0 1 .4 1 1V20c0 .6-.4 1-1 1A17 17 0 0 1 3 4c0-.6.4-1 1-1h3.5c.6 0 1 .4 1 1 0 1.3.2 2.5.6 3.6.1.3 0 .7-.2 1z"/></svg>
        <span>+61 487215963</span>
      </div>
      <div class="contact-line">
        <svg viewBox="0 0 24 24"><path d="M2 5h20v14H2z M2 5l10 7 10-7" fill="none" stroke="var(--brand-blue)" stroke-width="0"/><path d="M2 5h20v2l-10 6L2 7z"/><path d="M2 9l10 6 10-6v10H2z"/></svg>
        <span>dennis@quorv.com.au</span>
      </div>
      <div class="contact-line">
        <svg viewBox="0 0 24 24"><circle cx="12" cy="12" r="10"/><path d="M7 6c2 1 3 3 2 5s1 3 2 5M15 4c-1 2 0 4 2 4s3 2 3 4" fill="none" stroke="#f2f2f2" stroke-width="1.6"/></svg>
        <span>www.quorv.com.au</span>
      </div>
    </div>
    <div class="bottom-band"></div>
  </div>
</body>
</html>
```